Selfpublisher sucht Buch-/E-Book-Cover
Zielgruppe
Hallo
Ich bin Selfpublisher und schreibe gerade ein Buch mit dem Themeninhalt 'Grübeln Stoppen' und dafür benötige ich ein kreatives Ebook-Cover und Taschenbuchcover.
Aufgabenstellung
Ich habe detaillierte Vorgaben in meinem Template für den Designer vorbereitet.
Ein Stockphoto für die Covererstellung befindet sich ebenfalls im Anhang.

```html
<!DOCTYPE html>
<html lang="de">
<head>
<meta charset="utf-8">
<title>Raus aus der Gedankenschleife – Cover</title>
<link rel="stylesheet" href="https://fonts.googleapis.com/css2?family=Roboto:wght@300;400&family=Barlow+Semi+Condensed:wght@600;700&family=Fira+Sans+Condensed:wght@400&display=swap">
<style>
  :root {
    --ink: #111213;
    --white: #ffffff;
    --stop-red: #c8171c;
    --spine-pink: #c2317a;
    --spine-grey: #6b6f72;
    --wall-dark: #141618;
    --wall-mid: #4a4f4f;
    --floor: #1f2833;
  }
  * { margin: 0; padding: 0; box-sizing: border-box; }
  html, body { width: 1200px; height: 932px; overflow: hidden; background: #000; }
  .spread {
    position: relative; width: 1200px; height: 932px; overflow: hidden;
    font-family: "Roboto", sans-serif; color: var(--white);
  }
  .backdrop {
    position: absolute; inset: 0;
    background:
      radial-gradient(ellipse 360px 300px at 820px 330px, rgba(190,192,182,.75), rgba(120,124,118,0) 70%),
      radial-gradient(ellipse 700px 520px at 860px 420px, var(--wall-mid), rgba(40,44,46,0) 80%),
      linear-gradient(90deg, var(--wall-dark) 0%, #2c3030 30%, #3c4140 60%, #2e3233 100%);
  }
  .backdrop::after {
    content: ""; position: absolute; left: 0; right: 0; top: 770px; bottom: 0;
    background: linear-gradient(180deg, #2b323a 0%, var(--floor) 40%, #10151b 100%);
  }
  .spine-guide { position: absolute; top: 0; bottom: 0; width: 1px; }
  .spine-guide--left { left: 579px; background: var(--spine-pink); }
  .spine-guide--right { left: 621px; background: var(--spine-grey); }

  .back-cover { position: absolute; left: 62px; top: 88px; width: 478px; text-align: center; }
  .back-headline { font-weight: 400; font-size: 28px; line-height: 36px; }
  .back-body { margin-top: 16px; font-weight: 300; font-size: 17px; line-height: 26.7px; }
  .back-body + .back-body { margin-top: 26px; }
  .isbn-area { position: absolute; left: 327px; top: 755px; width: 222px; height: 134px; background: var(--white); }

  .spine-title {
    position: absolute; left: 601px; top: 303px;
    transform: translate(-50%, -50%) rotate(-90deg);
    white-space: nowrap; font-size: 17px; letter-spacing: .4px; font-weight: 400;
  }

  .title {
    position: absolute; left: 659px; top: 46px; width: 520px;
    font-family: "Barlow Semi Condensed", sans-serif; font-weight: 700;
    color: var(--ink); font-size: 92px; line-height: 80px; letter-spacing: 4px;
  }
  .title-line { display: flex; align-items: center; white-space: nowrap; height: 80px; }
  .title-small {
    margin-left: 22px; font-size: 30px; line-height: 27px; font-weight: 600; letter-spacing: .5px;
  }

  .stop-badge { position: absolute; left: 917px; top: 316px; width: 242px; height: 242px; transform: rotate(-8deg); }
  .stop-badge svg { position: absolute; inset: 0; }
  .stop-text {
    position: absolute; inset: 0; display: flex; align-items: center; justify-content: center; text-align: center;
    font-family: "Fira Sans Condensed", sans-serif; font-weight: 400; font-size: 21px; line-height: 25px; color: var(--white);
  }

  .author {
    position: absolute; right: 75px; top: 869px; white-space: nowrap;
    font-size: 25px; font-weight: 300; letter-spacing: .3px;
  }
</style>
</head>
<body>
<div class="spread">
  <div class="backdrop" role="img" aria-label="Stockfoto: junger Mann von hinten auf einem Stuhl vor einer Betonwand mit Fragezeichen und gekritzelten Gedankenschleifen, Kopfsteinpflaster am Boden"></div>

  <div class="spine-guide spine-guide--left"></div>
  <div class="spine-guide spine-guide--right"></div>

  <section class="back-cover">
    <h2 class="back-headline">Was ich im Alltag und im Beruf gelernt habe, zeigt dir einen neuen Weg.</h2>
    <p class="back-body">Nachdenken gehört zu jedem von uns. Manche tun es ständig, andere nur ab und zu. Schwierig wird es dann, wenn Sorgen, Erinnerungen und belastende Erlebnisse die Gedanken immer wieder im Kreis drehen lassen und kein Ausweg mehr sichtbar scheint. Auch ich kenne solche Phasen gut, habe vieles ausprobiert und dabei gesammelt, was mir geholfen hat, den Kopf wieder freizubekommen.</p>
    <p class="back-body">Dieses Buch bietet dir klare und alltagstaugliche Übungen, mit denen du deine Gedankenschleifen erkennst und ihnen eine neue Richtung gibst.</p>
  </section>
  <div class="isbn-area"></div>

  <div class="spine-title">RAUS AUS DER GEDANKENSCHLEIFE</div>

  <h1 class="title" aria-label="Raus aus der Gedankenschleife">
    <span class="title-line">RAUS<span class="title-small">AUS<br>DER</span></span>
    <span class="title-line">GEDANKEN-</span>
    <span class="title-line">SCHLEIFE</span>
  </h1>

  <div class="stop-badge">
    <svg viewBox="0 0 242 242" aria-hidden="true">
      <polygon points="71,0 171,0 242,71 242,171 171,242 71,242 0,171 0,71" fill="#ffffff"/>
      <polygon points="75,10 167,10 232,75 232,167 167,232 75,232 10,167 10,75" fill="var(--stop-red)"/>
    </svg>
    <p class="stop-text">Bewusst<br>Grübeln stoppen,<br>schlechte Gedanken<br>loswerden und lernen<br>die Gedanken-<br>schleife zu<br>kontrollieren.</p>
  </div>

  <p class="author">JONAS RIEDEL</p>
</div>
</body>
</html>
```